Business Postcard Design for Personal Training Company

Need a postcard design for my company called "Copperleaf Studio" Colors are Navy Blue, Blue, Grey and White.

On the front I want there to be pictures and it to feature a box that says "Free Consultation + 50% off your first session!"

And somehow to feature the following phrases " Lose Weight. Gain Muscle."
"Customized Personal training using Q-Pulse, the latest technology in fitness. Reach your fitness goals in just two 25-min sessions per week"

Also want featured the following phrases (maybe on back):

"up to 18 times more effective than a conventional gym workout"

I need the back of the postcard to have all my business information:

Address: 287 Wendover Ln, Building D Suite 318, Costa Mesa CA 92631
Website: copperleaf-studio.example
Phone #: (949) 555-0137
E-mail: copperleafwellness@mailbox.example

I am going to upload my logo, before and after pictures and pictures of people training on the device. Feel free to use as many/or little photos as you want.

Target Market(s)

Wealthy Adults 40+ years old looking for a personal trainer

Industry/Entity Type

Personal Trainer

Colors
0455a3
85cae6
aaaaaa
ffffff

Requirements
Must have
• At least two of the before and after photos, and two or more photos of people working out on the device.

```html
<!DOCTYPE html>
<html lang="en">
<head>
<meta charset="utf-8">
<title>Copperleaf Studio Postcards</title>
<link href="https://fonts.googleapis.com/css2?family=Fira+Sans:wght@500;600;700&family=Source+Sans+3:wght@400;600;700&display=swap" rel="stylesheet">
<style>
  :root {
    --navy: #0a4a96;
    --blue: #0455a3;
    --sky: #85cae6;
    --grey: #aaaaaa;
    --light: #f3f3f3;
    --text: #3a3a3a;
    --muted: #666666;
    --white: #ffffff;
    --backdrop: #e6e6e6;
  }
  * { margin: 0; padding: 0; box-sizing: border-box; }
  html, body { width: 834px; height: 1200px; overflow: hidden; background: var(--backdrop); }
  body { font-family: "Source Sans 3", "Helvetica Neue", Arial, sans-serif; color: var(--text); }
  .stage { position: relative; width: 916px; height: 1318px; transform: scale(0.9105); transform-origin: 0 0; }
  .postcard {
    position: absolute; left: 138px; width: 671px; height: 519px; overflow: hidden;
    background: var(--white); box-shadow: 0 4px 14px rgba(0,0,0,0.25);
  }
  .postcard--front { top: 118px; background: var(--light); }
  .postcard--back { top: 699px; }
  .postcard__shapes { position: absolute; inset: 0; width: 671px; height: 519px; }
  .brand { position: absolute; display: flex; align-items: center; gap: 8px; }
  .brand__dot { width: 16px; height: 16px; border-radius: 50%; background: var(--sky); }
  .brand__name { font-family: "Fira Sans", sans-serif; font-weight: 600; font-size: 19px; color: #7d8c99; letter-spacing: 0.5px; white-space: nowrap; }
  .headline { position: absolute; font-family: "Source Sans 3", sans-serif; font-weight: 700; color: var(--blue); white-space: nowrap; }
  .offer { position: absolute; left: 270px; top: 150px; width: 400px; text-align: center; color: var(--white); font-family: "Fira Sans", sans-serif; font-weight: 600; }
  .offer__main { font-size: 27px; letter-spacing: 1px; line-height: 1.3; }
  .offer__sub { font-size: 25px; line-height: 1.3; }
  .body-copy { position: absolute; font-size: 17px; line-height: 26px; }
  .address { position: absolute; left: 34px; color: var(--white); font-size: 15.5px; line-height: 20px; white-space: nowrap; }
  .contact { position: absolute; color: var(--blue); font-size: 17px; line-height: 24px; white-space: nowrap; }
  .contact strong { font-weight: 700; }
  .contact .phone { font-size: 20px; font-weight: 700; }
  .banner-text { position: absolute; left: 20px; top: 148px; width: 330px; text-align: center; color: var(--white); font-size: 14.5px; font-weight: 600; line-height: 19px; white-space: nowrap; }
  .photo-label { font-family: "Source Sans 3", sans-serif; font-weight: 700; fill: var(--white); letter-spacing: 1px; }
</style>
</head>
<body>
<div class="stage">

  <section class="postcard postcard--front">
    <svg class="postcard__shapes" viewBox="0 0 671 519">
      <defs>
        <linearGradient id="trainingPhotoTone" x1="0" y1="0" x2="1" y2="1">
          <stop offset="0" stop-color="#c9d3dd"/>
          <stop offset="0.5" stop-color="#6f8fb8"/>
          <stop offset="1" stop-color="#2a3f66"/>
        </linearGradient>
        <linearGradient id="resultTone" x1="0" y1="0" x2="0" y2="1">
          <stop offset="0" stop-color="#5a6f8f"/>
          <stop offset="1" stop-color="#2b3550"/>
        </linearGradient>
        <linearGradient id="offerBand" x1="0" y1="0" x2="1" y2="0">
          <stop offset="0" stop-color="#0a4a96"/>
          <stop offset="1" stop-color="#0455a3"/>
        </linearGradient>
      </defs>
      <g role="img" aria-label="Photo: trainer guiding a client exercising on a ball while wearing a muscle stimulation suit">
        <path d="M0,0 H385 C320,70 290,200 302,410 H0 Z" fill="url(#trainingPhotoTone)"/>
      </g>
      <path d="M255,142 H671 V238 H280 Z" fill="url(#offerBand)"/>
      <path d="M205,410 H671 V505 H240 Z" fill="var(--sky)"/>
      <path d="M0,420 H235 L245,519 H0 Z" fill="var(--blue)"/>
      <g transform="rotate(3 574 410)">
        <rect x="497" y="358" width="152" height="104" fill="var(--white)" style="filter:drop-shadow(0 2px 3px rgba(0,0,0,0.35))"/>
        <g role="img" aria-label="Before photo of a client">
          <rect x="502" y="363" width="70" height="94" fill="url(#resultTone)"/>
        </g>
        <g role="img" aria-label="After photo of the same client">
          <rect x="575" y="363" width="69" height="94" fill="url(#resultTone)"/>
        </g>
        <text class="photo-label" x="530" y="453" font-size="8">BEFORE</text>
        <text class="photo-label" x="604" y="453" font-size="8">AFTER</text>
      </g>
    </svg>

    <div class="brand" style="left:442px; top:45px;"><span class="brand__dot"></span><span class="brand__name">Copperleaf Studio</span></div>
    <h2 class="headline" style="left:290px; top:109px; width:380px; text-align:center; font-size:24px;">LOSE WEIGHT. GAIN MUSCLE.</h2>
    <div class="offer">
      <p class="offer__main">FREE CONSULTATION</p>
      <p class="offer__sub">+ 50% off your first session!</p>
    </div>
    <p class="body-copy" style="left:318px; top:248px; width:326px; text-align:center;">Customized Personal training using Q-Pulse, the latest technology in fitness. Reach your fitness goals in just two 25-min sessions per week</p>
    <p class="address" style="top:432px;">287 Wendover Ln,<br>Building D Suite 318,<br>Costa Mesa CA 92631</p>
    <p class="contact" style="left:243px; top:437px;">Call <span class="phone">(949) 555-0137</span> today<br>Or visit <strong>copperleaf-studio.example</strong> for information.</p>
  </section>

  <section class="postcard postcard--back">
    <svg class="postcard__shapes" viewBox="0 0 671 519">
      <defs>
        <linearGradient id="sessionPhotoTone" x1="0" y1="0" x2="1" y2="1">
          <stop offset="0" stop-color="#d6dde4"/>
          <stop offset="0.6" stop-color="#7b8ea8"/>
          <stop offset="1" stop-color="#2f3b55"/>
        </linearGradient>
        <linearGradient id="progressTone" x1="0" y1="0" x2="0" y2="1">
          <stop offset="0" stop-color="#e5e2dc"/>
          <stop offset="1" stop-color="#8a8782"/>
        </linearGradient>
      </defs>
      <path d="M0,118 H330 C395,130 408,250 405,402 H0 Z" fill="#e9e9e9"/>
      <g role="img" aria-label="Photo: trainer coaching a client in a side plank wearing a muscle stimulation suit">
        <path d="M0,190 H380 C392,260 395,330 392,402 H0 Z" fill="url(#sessionPhotoTone)"/>
      </g>
      <path d="M0,136 H386 L402,190 H0 Z" fill="var(--blue)"/>
      <g role="img" aria-label="Before photo of a client flexing">
        <rect x="402" y="125" width="125" height="275" fill="url(#progressTone)"/>
      </g>
      <g role="img" aria-label="After photo of the same client flexing">
        <rect x="533" y="125" width="138" height="275" fill="url(#progressTone)"/>
      </g>
      <text class="photo-label" x="410" y="388" font-size="11">BEFORE</text>
      <text class="photo-label" x="543" y="388" font-size="11">AFTER</text>
      <path d="M205,408 H671 V508 H240 Z" fill="var(--sky)"/>
      <path d="M0,420 H235 L245,519 H0 Z" fill="var(--blue)"/>
    </svg>

    <div class="brand" style="left:30px; top:58px;"><span class="brand__dot"></span><span class="brand__name">Copperleaf Studio</span></div>
    <h2 class="headline" style="right:16px; top:24px; font-size:20px; color:var(--navy);">A Healthier, Happier You</h2>
    <p class="body-copy" style="right:16px; top:53px; width:370px; text-align:right; font-size:15.5px; line-height:20px; color:var(--muted);">Customized Personal Training using Q-Pulse, an electro muscle stimulation device. Reach your goals in just two 25-min sessions per week!</p>
    <p class="banner-text">UP TO 18 TIMES MORE EFFECTIVE<br>THAN A CONVENTIONAL GYM WORKOUT</p>
    <p class="address" style="top:432px;">287 Wendover Ln,<br>Building D Suite 318,<br>Costa Mesa CA 92631</p>
    <p class="contact" style="left:245px; top:430px; width:420px; text-align:center; font-size:18px; line-height:28px;">Call <span class="phone" style="font-size:22px;">(949) 555-0137</span> today<br>Or visit <strong>copperleaf-studio.example</strong> for information.</p>
  </section>

</div>
</body>
</html>
```